RB Halden Electric Yard Sign

Looking to have a yard sign designed that we can place at projects we are working on. Most likely will be 18" H x 24" W but flexible that we can increase the size if necessary. It should include our logo, our phone # 609-555-0147, website rbhaldenelectric.example and slogan, built on integrity, driven by excellence. Colors should match our brand.

```html
<!DOCTYPE html>
<html lang="en">
<head>
<meta charset="utf-8">
<title>RB Halden Electric Yard Sign</title>
<link rel="stylesheet" href="https://fonts.googleapis.com/css2?family=Saira+Semi+Condensed:wght@600;700;800&display=swap">
<style>
  :root {
    --navy: #0b3368;
    --red: #ee1b2d;
    --white: #ffffff;
    --backdrop: #e9ecef;
  }
  * { box-sizing: border-box; margin: 0; padding: 0; }
  html, body {
    width: 1200px;
    height: 1029px;
    overflow: hidden;
    background: var(--backdrop);
  }
  .canvas {
    width: 1200px;
    height: 1029px;
    display: flex;
    align-items: center;
    justify-content: center;
  }
  .yard-sign {
    width: 1160px;
    height: 870px;
    background: var(--white);
    position: relative;
    display: flex;
    flex-direction: column;
    font-family: "Saira Semi Condensed", "Arial Narrow", sans-serif;
    box-shadow: 0 6px 24px rgba(0, 0, 0, 0.12);
  }
  .slogan-banner {
    height: 133px;
    margin: 0 43px;
    background: var(--navy);
    clip-path: polygon(0 0, 100% 0, 94.5% 100%, 5.4% 100%);
    display: flex;
    align-items: center;
    justify-content: center;
    overflow: hidden;
  }
  .slogan {
    color: var(--white);
    font-weight: 700;
    font-size: 44px;
    letter-spacing: -0.3px;
    line-height: 1;
    white-space: nowrap;
  }
  .brand {
    flex: 1;
    display: flex;
    align-items: center;
    justify-content: center;
    gap: 24px;
  }
  .brand-dot {
    flex: none;
    width: 50px;
    height: 50px;
    border-radius: 50%;
    background: var(--red);
  }
  .brand-name {
    color: var(--navy);
    font-weight: 800;
    font-size: 96px;
    line-height: 1;
    letter-spacing: 1px;
    white-space: nowrap;
  }
  .phone-band {
    height: 176px;
    background: var(--red);
    display: flex;
    align-items: center;
    justify-content: center;
    overflow: hidden;
  }
  .phone {
    color: var(--white);
    font-weight: 800;
    font-size: 146px;
    line-height: 1;
    letter-spacing: 3px;
    white-space: nowrap;
  }
  .web-band {
    height: 129px;
    background: var(--navy);
    display: flex;
    align-items: center;
    justify-content: center;
    overflow: hidden;
  }
  .website {
    color: var(--white);
    font-weight: 600;
    font-size: 60px;
    line-height: 1;
    white-space: nowrap;
  }
</style>
</head>
<body>
  <main class="canvas">
    <section class="yard-sign">
      <header class="slogan-banner">
        <p class="slogan">Built on Integrity, Driven by Excellence</p>
      </header>
      <div class="brand">
        <span class="brand-dot" aria-hidden="true"></span>
        <h1 class="brand-name">RB Halden Electric</h1>
      </div>
      <div class="phone-band">
        <p class="phone">609-555-0147</p>
      </div>
      <footer class="web-band">
        <p class="website">www.rbhaldenelectric.example</p>
      </footer>
    </section>
  </main>
</body>
</html>
```